Yard sign for Chimney Buisness

I am looking for a 18 Tall x 24" wide yard sign design incorporating our logo/name. We want the signs to stand out and be readable from a distance. only want our logo/business name and website on the sign . www.sootwardenspro.com

Target Market(s)

homeowners

Requirements
Must have
• logo/buisness name
• website
• must be visable at a distance and readable

```html
<!DOCTYPE html>
<html lang="en">
<head>
<meta charset="utf-8">
<title>Soot Wardens Yard Sign</title>
<link rel="stylesheet" href="https://fonts.googleapis.com/css2?family=Cinzel:wght@600&family=Lato:wght@400;700&display=swap">
<style>
  :root {
    --page-bg: #efefef;
    --sign-white: #ffffff;
    --sign-grey: #e6e6e6;
    --charcoal: #2d2d2d;
    --brand-red: #b30d10;
    --brand-red-deep: #870000;
    --silver-light: #f4f4f4;
    --silver-dark: #9a9a9a;
    --text-dark: #2b2b2b;
    --text-light: #ffffff;
  }
  * { margin: 0; padding: 0; box-sizing: border-box; }
  html, body {
    width: 1200px;
    height: 2247px;
    overflow: hidden;
    background: var(--page-bg);
  }
  .yard-sign {
    position: absolute;
    left: 50px;
    top: 711px;
    width: 1100px;
    height: 825px;
    box-shadow: 0 6px 24px rgba(0,0,0,0.18);
  }
  .sign-art {
    position: absolute;
    inset: 0;
    width: 100%;
    height: 100%;
    display: block;
  }
  .brand-lockup {
    position: absolute;
    left: 0;
    right: 0;
    top: 270px;
    display: flex;
    justify-content: center;
    align-items: center;
    gap: 26px;
  }
  .brand-mark {
    width: 58px;
    height: 58px;
    background: var(--charcoal);
  }
  .brand-name {
    font-family: "Cinzel", "Times New Roman", serif;
    font-weight: 600;
    font-size: 72px;
    letter-spacing: 1px;
    color: var(--text-dark);
    line-height: 1;
  }
  .contact {
    position: absolute;
    left: 0;
    right: 0;
    top: 640px;
    text-align: center;
    color: var(--text-light);
    font-family: "Lato", "Helvetica Neue", Arial, sans-serif;
  }
  .contact-phone {
    font-weight: 700;
    font-size: 84px;
    line-height: 1;
    letter-spacing: 1px;
  }
  .contact-web {
    margin-top: 14px;
    font-weight: 400;
    font-size: 42px;
    line-height: 1;
  }
  .contact-web strong { font-weight: 700; }
</style>
</head>
<body>
  <main class="yard-sign">
    <svg class="sign-art" viewBox="0 0 1000 750" preserveAspectRatio="none" aria-hidden="true">
      <defs>
        <linearGradient id="panel-fill" x1="0" y1="0" x2="1" y2="1">
          <stop offset="0" stop-color="var(--sign-white)"/>
          <stop offset="1" stop-color="var(--sign-grey)"/>
        </linearGradient>
        <linearGradient id="silver-fill" x1="0" y1="0" x2="1" y2="0">
          <stop offset="0" stop-color="var(--silver-dark)"/>
          <stop offset="0.6" stop-color="var(--silver-light)"/>
          <stop offset="1" stop-color="var(--silver-dark)"/>
        </linearGradient>
        <linearGradient id="red-fill" x1="0" y1="0" x2="1" y2="0">
          <stop offset="0" stop-color="var(--brand-red)"/>
          <stop offset="1" stop-color="var(--brand-red-deep)"/>
        </linearGradient>
      </defs>
      <rect class="sign-panel" width="1000" height="750" fill="url(#panel-fill)"/>
      <polygon class="charcoal-wedge" points="0,375 500,488 0,622" fill="var(--charcoal)"/>
      <polygon class="silver-swoosh" points="0,622 1000,372 1000,420" fill="url(#silver-fill)"/>
      <polygon class="red-band" points="0,622 1000,420 1000,750 0,750" fill="url(#red-fill)"/>
    </svg>

    <div class="brand-lockup">
      <span class="brand-mark"></span>
      <span class="brand-name">SOOT WARDENS</span>
    </div>

    <div class="contact">
      <p class="contact-phone">(802) 555-0147</p>
      <p class="contact-web">www.<strong>sootwardenspro</strong>.com</p>
    </div>
  </main>
</body>
</html>
```